Executive Business Card for Healthcare Company [Need Today]

I need a business card design for a healthcare company. The only branding the company has thus far is a logo. The cards will be utilized by company executives. The design I envision will be vibrant and appealing but with a corporate feel. They shouldn't be too casual or playful. I would like to complete this project TODAY if possible.

Target Market(s)

Healthcare vendors, other executives in healthcare and pharmaceuticals

Industry/Entity Type

Pharmaceutical

Contact Information for Business Card

See attachment

Font styles to use
Serif
Sans Serif

Colors

Designer to choose colors to be used in the design.

```html
<!DOCTYPE html>
<html lang="en">
<head>
<meta charset="utf-8">
<title>Corvane Therapeutics – Business Card</title>
<link rel="stylesheet" href="https://fonts.googleapis.com/css2?family=Roboto:wght@300;400;500&display=swap">
<style>
  :root {
    --backdrop: #e3e4e6;
    --card: #ffffff;
    --teal: #1fa9b8;
    --green: #3fb58f;
    --grey-text: #8c8e91;
    --dark-text: #4a4c4f;
    --band-grey: #6f7175;
    --rule: #b9bbbe;
  }
  * { margin: 0; padding: 0; box-sizing: border-box; }
  html, body { width: 1200px; height: 726px; overflow: hidden; }
  body {
    background: var(--backdrop);
    font-family: "Roboto", Arial, sans-serif;
    position: relative;
  }
  .card {
    position: absolute;
    top: 214px;
    width: 520px;
    height: 297px;
    background: var(--card);
    box-shadow: 0 10px 26px rgba(0,0,0,0.12);
    overflow: hidden;
  }
  .card--front { left: 48px; }
  .card--back { left: 632px; }

  .brand {
    display: flex;
    align-items: center;
    gap: 16px;
  }
  .brand__circle {
    border: 3px solid var(--green);
    border-radius: 50%;
    flex: none;
  }
  .brand__name {
    font-weight: 400;
    color: var(--teal);
    line-height: 1.15;
  }

  .card--front .brand {
    position: absolute;
    left: 0; right: 0; top: 92px;
    justify-content: center;
  }
  .card--front .brand__circle { width: 84px; height: 84px; }
  .card--front .brand__name { font-size: 34px; }
  .website {
    position: absolute;
    left: 0; right: 0; top: 218px;
    text-align: center;
    font-size: 14px;
    letter-spacing: 4px;
    color: var(--dark-text);
    font-weight: 300;
  }
  .website__domain { color: var(--teal); }

  .card--back .brand {
    position: absolute;
    left: 30px; top: 100px;
    gap: 12px;
  }
  .card--back .brand__circle { width: 62px; height: 62px; }
  .card--back .brand__name { font-size: 22px; }

  .contact {
    position: absolute;
    left: 318px; top: 78px;
    color: var(--dark-text);
  }
  .contact__name {
    font-size: 20px;
    font-weight: 500;
    color: var(--teal);
  }
  .contact__title {
    font-size: 9.5px;
    color: var(--grey-text);
    margin: 2px 0 10px 6px;
  }
  .contact__list { list-style: none; font-size: 12px; line-height: 19px; }
  .contact__list li { display: flex; align-items: center; gap: 8px; }
  .contact__list svg { width: 11px; height: 11px; fill: var(--dark-text); flex: none; }
  .contact__address { font-size: 12px; line-height: 17px; margin-top: 6px; }

  .band { position: absolute; left: 0; bottom: 0; width: 520px; height: 60px; }
</style>
</head>
<body>

<section class="card card--front" aria-label="Card front">
  <div class="brand">
    <span class="brand__circle"></span>
    <span class="brand__name">Corvane Therapeutics</span>
  </div>
  <p class="website">www.<span class="website__domain">corvanerx</span>.com</p>
</section>

<section class="card card--back" aria-label="Card back">
  <div class="brand">
    <span class="brand__circle"></span>
    <span class="brand__name">Corvane<br>Therapeutics</span>
  </div>

  <div class="contact">
    <h1 class="contact__name">Daniel Hale</h1>
    <p class="contact__title">Senior Director of Marketing</p>
    <ul class="contact__list">
      <li>
        <svg viewBox="0 0 12 12" aria-hidden="true"><path d="M1 4c0-2 1-3 5-3s5 1 5 3l-2 1-1-1.5H4L3 5 1 4zM2 6h8l1 5H1l1-5zm4 1.2a1.5 1.5 0 1 0 0 3 1.5 1.5 0 0 0 0-3z"/></svg>
        555-214-7730
      </li>
      <li>
        <svg viewBox="0 0 12 12" aria-hidden="true"><path d="M3 0h6a1 1 0 0 1 1 1v10a1 1 0 0 1-1 1H3a1 1 0 0 1-1-1V1a1 1 0 0 1 1-1zm0 1.5v8h6v-8H3zm3 8.6a.6.6 0 1 0 0 1.2.6.6 0 0 0 0-1.2z"/></svg>
        555-382-1946
      </li>
      <li>
        <svg viewBox="0 0 12 12" aria-hidden="true"><path d="M6 0a6 6 0 1 1 0 12A6 6 0 0 1 6 0zm-1 1.2A4.9 4.9 0 0 0 1.2 5H4c.1-1.5.4-2.8 1-3.8zm2 0c.6 1 .9 2.3 1 3.8h2.8A4.9 4.9 0 0 0 7 1.2zM5 5h2c-.1-1.6-.5-2.8-1-3.6C5.5 2.2 5.1 3.4 5 5zM1.2 7A4.9 4.9 0 0 0 5 10.8C4.4 9.8 4.1 8.5 4 7H1.2zM5 7c.1 1.6.5 2.8 1 3.6.5-.8.9-2 1-3.6H5zm3 0c-.1 1.5-.4 2.8-1 3.8A4.9 4.9 0 0 0 10.8 7H8z"/></svg>
        dhale@corvanerx.com
      </li>
    </ul>
    <p class="contact__address">518 Linden Avenue<br>Marlow, GA 30188</p>
  </div>

  <svg class="band" viewBox="0 0 520 60" aria-hidden="true">
    <defs>
      <linearGradient id="bandGradient" x1="0" x2="1" y1="0" y2="0">
        <stop offset="0" stop-color="#1fa9b8"/>
        <stop offset="1" stop-color="#3fb58f"/>
      </linearGradient>
    </defs>
    <polygon points="0,50 440,22 430,60 0,60" fill="url(#bandGradient)"/>
    <polygon points="446,22 520,18 520,60 436,60" fill="var(--band-grey)"/>
  </svg>
</section>

</body>
</html>
```